Business Cards for a law firm

Business cards for our law firm. Use our silhoette logo and OAK PARTNERS - check our website (www.oakpartners.example)

Contact Information for Business Card

our silhouette logo, OAK PARTNERS, 800-555-0147, Dorian Pemberton, dorian@oakpartners.example

Requirements
Must have
• our silhouette logo, OAK PARTNERS, 800-555-0147, Dorian Pemberton, dorian@oakpartners.example

```html
<!DOCTYPE html>
<html lang="en">
<head>
<meta charset="utf-8">
<title>Oak Partners — Business Cards</title>
<link href="https://fonts.googleapis.com/css2?family=Montserrat:wght@400;500;700&display=swap" rel="stylesheet">
<style>
  :root{
    --navy:#23306a;
    --white:#ffffff;
    --backdrop:#2b2b2d;
    --soft:#dfe3f2;
  }
  *{box-sizing:border-box;margin:0;padding:0}
  html,body{width:1200px;height:900px;overflow:hidden}
  body{background:var(--backdrop);font-family:"Montserrat",sans-serif;position:relative}
  .card{position:absolute;left:290px;width:620px;height:354px;border-radius:22px;overflow:hidden}
  .card--front{top:70px;background:var(--navy)}
  .card--back{top:476px;background:var(--white)}
  .brand{position:absolute;display:flex;align-items:center;gap:22px}
  .brand__mark{width:44px;height:44px}
  .brand__name{font-weight:400;font-size:40px;letter-spacing:5px;white-space:nowrap;line-height:1}
  .card--front .brand{left:70px;top:150px}
  .card--front .brand__mark{background:var(--white)}
  .card--front .brand__name{color:var(--white)}
  .card--back .brand{left:70px;top:70px}
  .card--back .brand__mark{background:var(--navy)}
  .card--back .brand__name{color:var(--navy)}
  .rule{position:absolute;left:0;right:0;top:190px;height:4px;background:var(--navy)}
  .band{position:absolute;left:0;right:0;top:204px;bottom:0;background:var(--navy);color:var(--white)}
  .person{position:absolute;right:330px;top:48px;text-align:right}
  .person__name{font-weight:700;font-size:24px;letter-spacing:.3px}
  .person__role{font-size:14px;margin-top:4px}
  .divider{position:absolute;left:312px;top:42px;width:1.5px;height:66px;background:var(--white)}
  .contact{position:absolute;left:334px;top:42px;list-style:none;font-size:14px;line-height:22px}
  .contact li{display:flex;align-items:center;gap:9px}
  .contact svg{width:12px;height:12px;flex:none}
</style>
</head>
<body>
  <section class="card card--front">
    <div class="brand">
      <span class="brand__mark"></span>
      <span class="brand__name">OAK PARTNERS</span>
    </div>
  </section>

  <section class="card card--back">
    <div class="brand">
      <span class="brand__mark"></span>
      <span class="brand__name">OAK PARTNERS</span>
    </div>
    <div class="rule"></div>
    <div class="band">
      <div class="person">
        <div class="person__name">Dorian Pemberton</div>
        <div class="person__role">Attorney at Law</div>
      </div>
      <div class="divider"></div>
      <ul class="contact">
        <li>
          <svg viewBox="0 0 12 12" aria-hidden="true"><path fill="#fff" d="M1 4c0-2 2-3 5-3s5 1 5 3v1H8V4H4v1H1zM3 6h6l2 5H1z"/></svg>
          800-555-0147
        </li>
        <li>
          <svg viewBox="0 0 12 12" aria-hidden="true"><rect x="0.5" y="2" width="11" height="8" fill="#fff"/><path d="M0.5 2l5.5 4.5L11.5 2" fill="none" stroke="#23306a" stroke-width="1"/></svg>
          dorian@oakpartners.example
        </li>
        <li>
          <svg viewBox="0 0 12 12" aria-hidden="true"><circle cx="6" cy="6" r="5.2" fill="none" stroke="#fff" stroke-width="1.3"/><ellipse cx="6" cy="6" rx="2.2" ry="5.2" fill="none" stroke="#fff" stroke-width="1"/><path d="M1 6h10" stroke="#fff" stroke-width="1"/></svg>
          www.oakpartners.example
        </li>
      </ul>
    </div>
  </section>
</body>
</html>
```